Wireless Internet Service Provider website design

We need a Internet Service Provider website that show the packages that we offer as well as the functionality where customers have the option of clicking on the various packages and be linked to a page where they can sign up for our services.
We need about 10-15 pages.
A. Integrated online store.
B. Live chat.
C. Social media page
My old website. Brightlinkradio.nyc

Example: http://plumcrestnet.com/services/residential/ Added Tuesday, June 7, 2016

Target Market(s)

Residential and small businesses

Industry/Entity Type

Internet

Coding

Coded - Design and coding required

Number of Pages Required

5+ page

Font styles to use
Serif
Sans Serif
Script

Colors
3176b5
85cae6
ffffff

Requirements
Must have
• Online store and live chat, drop down details on pricing from current website
Nice to have
• great design, functional website,

```html
<!DOCTYPE html>
<html lang="en">
<head>
<meta charset="utf-8">
<title>Brightlink Radio – Wireless Internet</title>
<link href="https://fonts.googleapis.com/css2?family=Open+Sans:ital,wght@0,400;0,600;0,700;1,400&family=Raleway:wght@500;600;700&display=swap" rel="stylesheet">
<style>
:root{
  --blue:#1d63a8;
  --blue-dark:#0f4f8e;
  --cyan:#1fb4d6;
  --cyan-light:#85cae6;
  --ink:#333a44;
  --muted:#6f7780;
  --line:#e3e7eb;
  --white:#ffffff;
}
*{box-sizing:border-box;margin:0;padding:0}
html,body{width:1200px;height:3614px;overflow:hidden;background:var(--white)}
body{position:relative;font-family:"Open Sans",Arial,sans-serif;color:var(--ink);font-size:13px}
.abs{position:absolute}
h1,h2,h3{font-family:"Raleway","Open Sans",sans-serif}

/* header */
.site-header{left:0;top:0;width:1200px;height:115px;background:var(--white);z-index:5}
.brand{left:96px;top:30px;display:flex;align-items:center;gap:10px;font-weight:700;font-size:22px;color:var(--blue)}
.brand-mark{width:26px;height:26px;background:var(--blue);display:block}
.top-util{top:20px;left:700px;display:flex;align-items:center;font-size:13px;color:var(--muted)}
.top-util b{color:var(--blue);font-weight:600}
.main-nav{top:72px;left:452px;display:flex;font-size:13px;font-weight:600;color:var(--ink)}
.main-nav span{padding:0 26px}
.dropdown{left:640px;top:104px;width:182px;background:var(--white);box-shadow:0 3px 10px rgba(0,0,0,.18);padding:6px 0;z-index:6}
.dropdown div{padding:10px 22px;font-size:12px;color:var(--muted);border-bottom:1px solid var(--line)}
.dropdown div:last-child{border:none}

/* hero */
.hero-photo{left:0;top:115px;width:1200px;height:613px;background:linear-gradient(100deg,#4a3b32 0%,#8a7566 35%,#6b5d54 60%,#3b3836 100%)}
.hero-shade{left:0;top:115px;width:1200px;height:613px;background:rgba(20,22,26,.35)}
.hero-title{left:0;top:292px;width:1200px;text-align:center;color:var(--white);font-size:34px;font-weight:700}
.hero-lead{left:360px;top:348px;width:480px;text-align:center;color:var(--white);font-size:15px;line-height:24px}
.btn{background:var(--cyan);color:var(--white);font-weight:600;text-align:center;border-radius:3px}
.hero-btn{left:496px;top:432px;width:210px;height:48px;line-height:48px;font-size:15px}
.hero-feature{top:555px;width:250px;text-align:center;color:var(--white);font-weight:700;font-size:14px;line-height:20px}
.hero-feature svg{display:block;margin:0 auto 20px}

/* welcome */
.welcome-title{left:0;top:790px;width:1200px;text-align:center;font-size:30px;color:var(--blue-dark);font-weight:700}
.welcome-text{left:0;top:850px;width:1200px;text-align:center;font-size:12px;color:var(--muted)}
.service{top:928px;width:240px;text-align:center;color:var(--cyan);font-size:15px}
.service .ring{width:130px;height:130px;border:1.5px solid var(--cyan);border-radius:50%;margin:0 auto 26px;display:flex;align-items:center;justify-content:center}

/* speed band */
.speed-photo{left:0;top:1171px;width:1200px;height:463px;background:linear-gradient(90deg,#1c2126 0%,#2f363d 45%,#707a82 75%,#3c4248 100%)}
.speed-title{left:100px;top:1295px;width:520px;color:var(--white);font-size:28px;line-height:38px;font-weight:700}
.speed-text{left:100px;top:1390px;width:560px;color:#e6e9ec;font-size:14px;line-height:26px}

/* plans */
.plans-title{left:0;top:1694px;width:1200px;text-align:center;font-size:31px;color:var(--blue-dark);font-weight:700}
.plans-intro{left:170px;top:1756px;width:860px;text-align:center;font-size:12px;line-height:22px;color:var(--muted)}
.plan{top:1863px;width:320px;height:518px;border:1px solid var(--line);background:var(--white);box-shadow:0 1px 4px rgba(0,0,0,.06)}
.plan-head{height:125px;background:linear-gradient(180deg,#1f6bb5,#0f4f8e);color:var(--white);text-align:center;padding-top:20px}
.plan-head .speed{font-size:22px;font-weight:700;font-family:"Raleway",sans-serif}
.plan-head .sub{font-size:16px;margin-top:2px}
.plan-head .name{font-size:22px;font-weight:700;margin-top:4px}
.plan-body{padding:22px 30px 0}
.plan-body .desc{font-size:12px;line-height:20px;color:var(--muted);padding-bottom:14px;border-bottom:1px solid var(--line)}
.plan-body li{list-style:none;font-size:12px;font-weight:600;color:var(--ink);padding:14px 0 14px 22px;border-bottom:1px solid var(--line);position:relative}
.plan-body li::before{content:"";position:absolute;left:2px;top:20px;width:7px;height:7px;border:1px solid #9aa2aa;border-radius:50%}
.price{text-align:center;margin-top:22px;color:var(--blue-dark);font-weight:700;font-size:46px;line-height:50px}
.price small{font-size:28px}
.plan-btn{margin:14px auto 0;width:264px;height:54px;line-height:54px;font-size:20px}
.carousel-arrow{top:2100px}

/* testimonials */
.testimonial-photo{left:0;top:2439px;width:1200px;height:424px;background:linear-gradient(90deg,#1b1e22,#3a3f45 60%,#24282c)}
.testimonial-title{left:0;top:2512px;width:1200px;text-align:center;color:var(--white);font-size:30px;font-weight:700}
.quote{left:229px;top:2604px;width:500px;color:#dfe3e6;font-style:italic;font-size:14px;line-height:26px}
.quote-mark{left:196px;top:2596px;color:var(--muted);font-size:40px;font-family:Georgia,serif}
.client{left:229px;top:2726px;font-size:13px;line-height:22px}
.client b{color:var(--cyan);font-weight:600;display:block}
.client span{color:#c8cdd2}
.portrait{left:793px;top:2591px;width:178px;height:178px;border-radius:50%;background:linear-gradient(135deg,#c9a88a,#6e5a4a);border:3px solid rgba(255,255,255,.7)}

/* map */
.map{left:0;top:2863px;width:1200px;height:318px;background:linear-gradient(160deg,#34587a,#264560 60%,#1f3a52)}
.map-tabs{left:8px;top:2873px;display:flex;background:var(--white);font-size:10px;box-shadow:0 1px 3px rgba(0,0,0,.3)}
.map-tabs span{padding:5px 8px}
.map-zoom{left:1172px;top:3108px;width:20px;height:44px;background:var(--white);border-radius:2px;font-size:14px;text-align:center;line-height:22px}

/* footer */
.footer-col{top:3232px}
.footer-col h3{font-size:16px;color:var(--blue-dark);font-weight:700;margin-bottom:18px}
.newsletter p{font-size:12px;color:var(--muted);margin-bottom:16px}
.email-field{width:312px;height:38px;border:1px solid #cfd5da;font-size:12px;color:#a0a7ae;padding:10px 12px}
.subscribe{margin-top:14px;width:140px;height:38px;line-height:38px;font-size:14px}
.footer-brand{left:99px;top:3435px;display:flex;align-items:center;gap:10px;font-size:24px;font-weight:700;color:var(--blue)}
.footer-links div{font-size:12px;color:var(--muted);line-height:25px}
.contact div{font-size:12px;color:var(--muted);line-height:22px}
.contact .row{display:flex;align-items:center;gap:8px;margin-top:6px}
.socials{display:flex;gap:10px;margin-top:14px}
.socials span{width:30px;height:30px;border-radius:50%;display:block}
.bottom-bar{left:0;top:3557px;width:1200px;height:57px;border-top:1px solid var(--line);text-align:center;font-size:12px;color:var(--muted);line-height:56px}
.bottom-bar span{margin-left:26px}
.live-chat{left:1015px;top:3494px;width:178px;height:54px;background:var(--blue);color:var(--white);border-radius:4px 4px 0 0;display:flex;align-items:center;gap:10px;padding-left:20px}
.live-chat b{display:block;font-size:15px}
.live-chat small{font-size:10px}
</style>
</head>
<body>

<header class="site-header abs">
  <div class="brand abs"><span class="brand-mark"></span>Brightlink Radio</div>
  <div class="top-util abs">
    <svg width="16" height="16" viewBox="0 0 16 16"><circle cx="7" cy="7" r="5" fill="none" stroke="#9aa2aa" stroke-width="1.6"/><line x1="11" y1="11" x2="15" y2="15" stroke="#9aa2aa" stroke-width="1.6"/></svg>
    <span style="margin-left:30px"><svg width="12" height="12" viewBox="0 0 12 12"><path d="M2 1h3l1 3-2 1a7 7 0 0 0 3 3l1-2 3 1v3c-5 1-10-4-9-9z" fill="#1d63a8"/></svg> Call Us : <b>(866) 555-0142</b></span>
    <span style="margin-left:50px"><svg width="18" height="14" viewBox="0 0 18 14"><path d="M1 1h3l2 8h9l2-6H5" fill="none" stroke="#1d63a8" stroke-width="1.5"/><circle cx="7" cy="12" r="1.4" fill="#1d63a8"/><circle cx="14" cy="12" r="1.4" fill="#1d63a8"/></svg> Your cart is <b>0 items</b></span>
  </div>
  <nav class="main-nav abs">
    <span>Home</span><span>Why Brightlink</span><span>Plans &amp; Packages ⌄</span><span>My Account</span><span>Gallery</span><span>Contacts</span>
  </nav>
</header>
<div class="dropdown abs"><div>›&nbsp; FAQs</div><div>›&nbsp; Testimonials</div><div>›&nbsp; Sitemap</div></div>

<section class="hero">
  <div class="hero-photo abs" role="img" aria-label="Photo of a smiling woman working on a laptop in a bright room"></div>
  <div class="hero-shade abs"></div>
  <h1 class="hero-title abs">Finally, the internet you deserve is here</h1>
  <p class="hero-lead abs">Welcome to Brightlink's fiber-speed network without fiber – the new choice for those of you who don't feel you have a lot of choices.</p>
  <div class="btn hero-btn abs">Find the best deals</div>
  <svg class="abs" style="left:48px;top:400px" width="30" height="30" viewBox="0 0 30 30"><circle cx="15" cy="15" r="14" fill="none" stroke="rgba(255,255,255,.4)"/><path d="M17 9l-6 6 6 6" stroke="rgba(255,255,255,.6)" fill="none" stroke-width="1.5"/></svg>
  <svg class="abs" style="left:1122px;top:400px" width="30" height="30" viewBox="0 0 30 30"><circle cx="15" cy="15" r="14" fill="none" stroke="rgba(255,255,255,.4)"/><path d="M13 9l6 6-6 6" stroke="rgba(255,255,255,.6)" fill="none" stroke-width="1.5"/></svg>
  <div class="hero-feature abs" style="left:200px">
    <svg width="56" height="56" viewBox="0 0 56 56" fill="none" stroke="#fff" stroke-width="2"><rect x="8" y="30" width="40" height="14" rx="2"/><line x1="28" y1="30" x2="28" y2="18"/><path d="M20 16a11 11 0 0 1 16 0M15 11a18 18 0 0 1 26 0"/><circle cx="16" cy="37" r="1.5" fill="#fff"/><circle cx="22" cy="37" r="1.5" fill="#fff"/></svg>
    Residential Internet<br>Access
  </div>
  <div class="hero-feature abs" style="left:475px">
    <svg width="56" height="56" viewBox="0 0 56 56" fill="none" stroke="#fff" stroke-width="2"><rect x="12" y="6" width="18" height="44"/><rect x="30" y="20" width="14" height="30"/><path d="M17 14h8M17 22h8M17 30h8M17 38h8M35 28h4M35 36h4"/></svg>
    Business Internet<br>Access
  </div>
  <div class="hero-feature abs" style="left:750px">
    <svg width="56" height="56" viewBox="0 0 56 56" fill="none" stroke="#fff" stroke-width="2"><circle cx="28" cy="28" r="21"/><ellipse cx="28" cy="28" rx="9" ry="21"/><path d="M7 28h42M11 17h34M11 39h34"/></svg>
    Unlimited Internet<br>Usage
  </div>
</section>

<section class="welcome">
  <h2 class="welcome-title abs">Welcome to Brightlink Radio</h2>
  <p class="welcome-text abs">Brightlink is a company that provides Residential and Businesses access to the Internet and other related services such as VOIP and WiFi.</p>
  <div class="service abs" style="left:217px">
    <div class="ring"><svg width="60" height="60" viewBox="0 0 60 60" fill="none" stroke="#1fb4d6" stroke-width="2"><path d="M14 32v-6a16 16 0 0 1 32 0v6"/><rect x="10" y="30" width="8" height="13" rx="3"/><rect x="42" y="30" width="8" height="13" rx="3"/><path d="M46 43c0 6-6 8-12 8"/><rect x="28" y="48" width="8" height="5" rx="2"/></svg></div>
    Customer support center
  </div>
  <div class="service abs" style="left:482px">
    <div class="ring"><svg width="60" height="60" viewBox="0 0 60 60" fill="none" stroke="#1fb4d6" stroke-width="2"><path d="M14 46l18-18M10 50l6-2 2-6-4-2z"/><path d="M38 10a9 9 0 0 0-8 12l-18 18 6 6 18-18a9 9 0 0 0 12-8l-5 4-5-2-2-5z"/><path d="M30 34l14 14 4-4-14-14"/></svg></div>
    Equipment Options
  </div>
  <div class="service abs" style="left:760px">
    <div class="ring"><svg width="60" height="60" viewBox="0 0 60 60" fill="none" stroke="#1fb4d6" stroke-width="2"><path d="M30 8l18 6v14c0 12-8 20-18 24C20 48 12 40 12 28V14z"/><path d="M21 30l7 7 12-13"/></svg></div>
    Customer guarantee
  </div>
</section>

<section class="speed">
  <div class="speed-photo abs" role="img" aria-label="Photo of a man in glasses working at a laptop"></div>
  <h2 class="speed-title abs">Fast download &amp; upload speeds at an affordable price</h2>
  <p class="speed-text abs">When choosing among the best high speed Internet providers, there are several other factors that should be taken into consideration besides just the available download speeds. Upload speeds are important as well, though they probably are not as crucial as download speeds.</p>
</section>

<section class="plans">
  <h2 class="plans-title abs">Plan &amp; packages</h2>
  <p class="plans-intro abs">Brightlink has a range of affordable plans that provide New Yorker with the best wireless Internet service. Plans provide up to 500 Mbps download speeds, unlimited Internet usage per month, in most areas, we have plans starting at just $39.99 per month. For plan deals, pricing and availability of packages in your area enter your address below.</p>

  <div class="plan abs" style="left:99px">
    <div class="plan-head"><div class="speed">5 Mbps</div><div class="sub">Download Speed</div><div class="name">Brightlink Simplicity</div></div>
    <div class="plan-body">
      <div class="desc">The right speed for occasional Internet usage, including checking emails, social networks and light internet browsing...</div>
      <ul><li>Free smart router</li><li>Free internet protection</li><li>Unlimited Brightlink Wi-Fi access</li></ul>
    </div>
    <div class="price">$39<small>.99</small></div>
    <div class="btn plan-btn">Signup now</div>
  </div>
  <div class="plan abs" style="left:441px">
    <div class="plan-head"><div class="speed">10 Mbps</div><div class="sub">Download Speed</div><div class="name">Brightlink Value Pak</div></div>
    <div class="plan-body">
      <div class="desc">The right speed for occasional Internet usage, including checking emails, social networks and light internet browsing...</div>
      <ul><li>Free smart router</li><li>Free internet protection</li><li>Unlimited Brightlink Wi-Fi access</li></ul>
    </div>
    <div class="price">$45<small>.99</small></div>
    <div class="btn plan-btn">Signup now</div>
  </div>
  <div class="plan abs" style="left:781px">
    <div class="plan-head"><div class="speed">25 Mbps</div><div class="sub">Download Speed</div><div class="name">Brightlink Super-Pak</div></div>
    <div class="plan-body">
      <div class="desc">The right speed for occasional Internet usage, including checking emails, social networks and light internet browsing...</div>
      <ul><li>Free smart router</li><li>Free internet protection</li><li>Unlimited Brightlink Wi-Fi access</li></ul>
    </div>
    <div class="price">$69<small>.99</small></div>
    <div class="btn plan-btn">Signup now</div>
  </div>
  <svg class="carousel-arrow abs" style="left:42px" width="16" height="40" viewBox="0 0 16 40"><path d="M14 2L2 20l12 18" fill="none" stroke="#c4cad0" stroke-width="2"/></svg>
  <svg class="carousel-arrow abs" style="left:1140px" width="16" height="40" viewBox="0 0 16 40"><path d="M2 2l12 18-12 18" fill="none" stroke="#c4cad0" stroke-width="2"/></svg>
</section>

<section class="testimonials">
  <div class="testimonial-photo abs" role="img" aria-label="Dark photo of hands typing on a laptop keyboard"></div>
  <h2 class="testimonial-title abs">Testimonials</h2>
  <div class="quote-mark abs">“</div>
  <p class="quote abs">Thanks for your great service. I love my internet and your quick response to my questions and concerns. I would definitely refer Brightlink to my friends and family. Keep up the good work.</p>
  <div class="client abs"><b>Marcus Ellery</b><span>Client</span></div>
  <div class="portrait abs" role="img" aria-label="Portrait photo of the client"></div>
</section>

<section class="location">
  <div class="map abs" role="img" aria-label="Map of New York City and surrounding area with office location pin in Brooklyn"></div>
  <div class="map-tabs abs"><span style="font-weight:700">Map</span><span style="color:#777">Satellite</span></div>
  <svg class="abs" style="left:592px;top:2980px" width="22" height="32" viewBox="0 0 22 32"><path d="M11 31C4 20 1 16 1 11a10 10 0 0 1 20 0c0 5-3 9-10 20z" fill="#e2463b"/><circle cx="11" cy="11" r="3.5" fill="#8a1f18"/></svg>
  <div class="map-zoom abs">+<br>−</div>
</section>

<footer>
  <div class="footer-col newsletter abs" style="left:99px">
    <h3>Newsletter signup</h3>
    <p>Sign up to our newsletter to receive our news &amp; events</p>
    <div class="email-field">Enter your email id</div>
    <div class="btn subscribe">Subscribe</div>
  </div>
  <div class="footer-brand abs"><span class="brand-mark" style="width:30px;height:30px"></span>Brightlink Radio</div>

  <div class="footer-col footer-links abs" style="left:537px">
    <h3>Welcome</h3>
    <div>Refer a friend</div><div>Free Internet for life</div><div>Terms &amp; Conditions</div><div>Privacy Policy</div><div>Site Map</div><div>Wireless Internet Access Agreement</div><div>Brightlink Internet Access</div><div>Customer Support Center</div><div>Catalog</div>
  </div>

  <div class="footer-col contact abs" style="left:852px">
    <h3>Contact info</h3>
    <div>2150 Harbor Street</div>
    <div>2nd Fl. Brooklyn, NY 11201</div>
    <div class="row"><svg width="12" height="12" viewBox="0 0 12 12"><path d="M2 1h3l1 3-2 1a7 7 0 0 0 3 3l1-2 3 1v3c-5 1-10-4-9-9z" fill="#1d63a8"/></svg>866-555-0142</div>
    <div class="row"><svg width="12" height="10" viewBox="0 0 12 10"><rect x="0.5" y="0.5" width="11" height="9" fill="none" stroke="#1d63a8"/><path d="M1 1l5 4 5-4" fill="none" stroke="#1d63a8"/></svg>support@brightlinkradio.nyc</div>
    <div style="padding-left:20px">sales@brightlinkradio.nyc</div>
    <div class="socials"><span style="background:#3b5a98"></span><span style="background:#3fa9e0"></span><span style="background:#d0312d"></span><span style="background:#d6493a"></span></div>
  </div>

  <div class="bottom-bar abs">© 2016. Brightlink Radio. All rights reserved.<span>Privacy Policy</span></div>
  <div class="live-chat abs">
    <svg width="24" height="22" viewBox="0 0 24 22"><path d="M2 2h14v9H7l-4 3v-3H2z" fill="#fff"/><path d="M18 6h4v9h-1v3l-4-3h-7v-2h8z" fill="#fff" opacity=".7"/></svg>
    <div><b>Live chat</b><small>24 hours support</small></div>
  </div>
</footer>

</body>
</html>
```